design a construction company business card

Design business card around our logo. Card must have all the typical info: name, title, address, phone, email, business name, etc. Somewhere on the card I would like to see our motto "Built on integrity... Inspired by commitment." Consider adding a splash of bright orange to the card to complement the blues and silvers/grays in the logo. We are open to metallic inks, textures, etc. We would like to see options on both light and dark backgrounds. The font in the logo is Euro Technic Extended Regular.

```html
<!DOCTYPE html>
<html lang="en">
<head>
<meta charset="utf-8">
<title>Halden Contracting – Business Card</title>
<link rel="stylesheet" href="https://fonts.googleapis.com/css2?family=Lato:wght@400;700&display=swap">
<style>
  :root {
    --backdrop: #555555;
    --card-white: #ffffff;
    --brand-blue: #1f4ea8;
    --blue-top: #1a6fba;
    --blue-bottom: #263f99;
    --ink: #1b1b1b;
    --on-blue: #ffffff;
  }
  html, body {
    margin: 0;
    padding: 0;
    width: 1200px;
    height: 900px;
    overflow: hidden;
    background: var(--backdrop);
    font-family: "Lato", sans-serif;
  }
  .stage {
    position: relative;
    width: 1200px;
    height: 900px;
  }
  .card {
    position: absolute;
    top: 200px;
    width: 310px;
    height: 502px;
    box-sizing: border-box;
  }
  .card-front {
    left: 253px;
    background: var(--card-white);
    border-radius: 56px 0 56px 0;
  }
  .card-back {
    left: 627px;
    background: linear-gradient(to bottom, var(--blue-top), var(--blue-bottom));
    border-radius: 0 56px 0 56px;
    color: var(--on-blue);
  }
  .wordmark {
    position: absolute;
    left: 0;
    right: 0;
    text-align: center;
    font-weight: 700;
    text-transform: uppercase;
    line-height: 1;
  }
  .wordmark .name {
    display: block;
    font-size: 46px;
    letter-spacing: 3px;
  }
  .wordmark .suffix {
    display: block;
    font-size: 15px;
    letter-spacing: 2px;
    margin-top: 8px;
  }
  .card-front .wordmark { top: 156px; color: var(--brand-blue); }
  .card-back .wordmark { top: 218px; color: var(--on-blue); }

  .contact {
    position: absolute;
    left: 32px;
    top: 327px;
    color: var(--ink);
    font-size: 14px;
    line-height: 18px;
  }
  .contact .person {
    margin: 0 0 0 3px;
    font-size: 18px;
    font-weight: 700;
    color: var(--brand-blue);
    line-height: 20px;
  }
  .contact .role { margin: 0 0 8px 3px; }
  .contact ul { list-style: none; margin: 0; padding: 0; }
  .contact li { display: flex; align-items: center; gap: 5px; }
  .contact li svg { width: 12px; height: 12px; fill: var(--brand-blue); }
  .contact address { font-style: normal; margin-top: 8px; }

  .motto {
    position: absolute;
    left: 0;
    right: 0;
    top: 412px;
    margin: 0;
    text-align: center;
    font-size: 15.5px;
    line-height: 20px;
    text-transform: uppercase;
  }
</style>
</head>
<body>
<main class="stage">
  <section class="card card-front">
    <div class="wordmark">
      <span class="name">Halden</span>
      <span class="suffix">Contracting, Inc.</span>
    </div>
    <div class="contact">
      <p class="person">MARCUS HALE</p>
      <p class="role">Managing Director</p>
      <ul>
        <li>
          <svg viewBox="0 0 12 12" aria-hidden="true"><path d="M1 4c0-2 2-3 5-3s5 1 5 3l-2 1-1-1.5H4L3 5zM2.5 6h7l1 5h-9z"/></svg>
          044-123 456 789
        </li>
        <li>
          <svg viewBox="0 0 12 12" aria-hidden="true"><path d="M1 2.5h10v7H1z M1.5 3l4.5 3.5L10.5 3" stroke="#fff" stroke-width=".8"/></svg>
          info@webname.com
        </li>
        <li>
          <svg viewBox="0 0 12 12" aria-hidden="true"><circle cx="6" cy="6" r="5"/></svg>
          www.websitename.com
        </li>
      </ul>
      <address>12345, Address Goes Here<br>Country Name, 123456</address>
    </div>
  </section>

  <section class="card card-back">
    <div class="wordmark">
      <span class="name">Halden</span>
      <span class="suffix">Contracting, Inc.</span>
    </div>
    <p class="motto">Built on integrity... Inspired<br>by commitment</p>
  </section>
</main>
</body>
</html>
```